Marlowe Group needs a business card

I would like the card to be simple but modern and elegant.
I like black and white.
or black and gold.
we are a private finance lender and also are involved in property and property developments.

please look at the business card photos i provided i would like M.G only one one side and all the other details on the other side use fonts that tie in with my theme.

Industry/Entity Type

Finance

Contact Information for Business Card

Marlowe Group (M.G) Daniel Marlowe M: 0413586207 E: danmarl@inboxmail.test

Font styles to use
Other font styles liked:
• Use fonts that would reflect our business

Colors
000000
ffffff

Requirements
Must have
• one side of details
• other side has either M.G or Marlowe Group like in the photos provided

```html
<!DOCTYPE html>
<html lang="en">
<head>
<meta charset="utf-8">
<title>Marlowe Group – Business Card</title>
<link rel="stylesheet" href="https://fonts.googleapis.com/css2?family=Open+Sans:ital,wght@0,400;0,600;0,700;0,800;1,400&display=swap">
<style>
  :root {
    --gold: #d2a023;
    --gold-deep: #c99a1e;
    --black: #111111;
    --white: #ffffff;
    --ink: #444444;
    --backdrop: #e9e7e3;
  }
  * { margin: 0; padding: 0; box-sizing: border-box; }
  html, body {
    width: 1200px;
    height: 987px;
    overflow: hidden;
    background: var(--backdrop);
    font-family: "Open Sans", Arial, sans-serif;
  }
  .stage {
    position: relative;
    width: 1200px;
    height: 987px;
  }
  .card {
    position: absolute;
    left: 293px;
    width: 615px;
    height: 351px;
    box-shadow: 0 4px 10px rgba(0,0,0,0.18);
    overflow: hidden;
  }
  .card-front { top: 130px; background: var(--white); }
  .card-back  { top: 505px; }

  .brand-name {
    position: absolute;
    left: 27px;
    top: 44px;
    font-size: 32px;
    font-weight: 800;
    letter-spacing: 1px;
    color: var(--gold);
    text-transform: uppercase;
    line-height: 1;
  }

  .contact {
    position: absolute;
    right: 31px;
    top: 228px;
    text-align: right;
    color: var(--ink);
  }
  .contact-name {
    font-size: 22px;
    font-weight: 600;
    color: var(--gold);
    line-height: 1.2;
    margin-bottom: 8px;
  }
  .contact-line {
    font-size: 15.5px;
    line-height: 1.5;
  }
  .contact-label {
    font-weight: 700;
    color: var(--gold);
  }

  .front-bands {
    position: absolute;
    left: 0;
    bottom: 0;
    width: 615px;
    height: 36px;
  }
  .web-address {
    position: absolute;
    right: 31px;
    bottom: 12px;
    font-size: 15px;
    font-style: italic;
    color: var(--white);
    letter-spacing: 0.3px;
  }

  .back-fill {
    position: absolute;
    inset: 0;
    background: linear-gradient(135deg, var(--gold) 0%, var(--gold-deep) 100%);
  }
  .monogram {
    position: absolute;
    inset: 0;
    display: flex;
    align-items: center;
    justify-content: center;
    font-size: 96px;
    font-weight: 800;
    color: var(--black);
    letter-spacing: 2px;
    transform: scaleX(1.25);
  }
</style>
</head>
<body>
<main class="stage">

  <section class="card card-front" aria-label="Business card, front">
    <div class="brand-name">Marlowe Group</div>

    <div class="contact">
      <div class="contact-name">Daniel Marlowe</div>
      <div class="contact-line"><span class="contact-label">Cell :</span> 0413586207</div>
      <div class="contact-line">danmarl@inboxmail.test</div>
    </div>

    <svg class="front-bands" viewBox="0 0 615 36" aria-hidden="true">
      <polygon points="0,22 336,22 328,36 0,36" fill="var(--black)"/>
      <polygon points="355,0 615,0 615,36 328,36" fill="var(--gold)"/>
    </svg>
    <div class="web-address">www.marlowegroup.test</div>
  </section>

  <section class="card card-back" aria-label="Business card, back">
    <div class="back-fill" role="img" aria-label="Gold background with faint repeating monogram pattern"></div>
    <div class="monogram">M.G</div>
  </section>

</main>
</body>
</html>
```